Hvac and insulation company needs good looking business card design

We are hvac and insulation company and looking for a new business cards that look to today standards designs

Target Market(s)

homeowners

Industry/Entity Type

Hvac

Contact Information for Business Card

Name: Walter Brinoku
Home comfort consultant
address: 4827 Dunmore St #215 Oakland, CA 94619
office: 888-316-2790
cell: 510-742-3185
Lic.# 584261
Email: walter@corvane-hvac.com
Web: corvane-hvac.com

Requirements
Must have
• clean and sleek look
Nice to have
• simple with a clean look
Should not have
• to busy business card

```html
<!DOCTYPE html>
<html lang="en">
<head>
<meta charset="utf-8">
<title>Corvane – Business Card</title>
<link rel="stylesheet" href="https://fonts.googleapis.com/css2?family=Open+Sans:wght@300;400;600;800&display=swap">
<style>
  :root {
    --backdrop: #2b2b2c;
    --card: #1f1f20;
    --card-edge: #262627;
    --orange: #ef8a12;
    --white: #f2f2f2;
  }
  * { margin: 0; padding: 0; box-sizing: border-box; }
  html, body {
    width: 1200px; height: 900px; overflow: hidden;
    background: var(--backdrop);
    font-family: "Open Sans", Arial, sans-serif;
  }
  .canvas {
    width: 1200px; height: 900px;
    display: flex; flex-direction: column; align-items: center; justify-content: center;
    gap: 36px;
    background: radial-gradient(ellipse at 60% 30%, #3a3a3b 0%, var(--backdrop) 70%);
  }
  .card {
    position: relative;
    width: 700px; height: 400px;
    background: linear-gradient(135deg, var(--card-edge), var(--card));
    box-shadow: 0 14px 30px rgba(0,0,0,.45);
    color: var(--white);
  }
  .company-name {
    display: flex; align-items: center; gap: 14px;
    color: var(--white); font-weight: 600; line-height: 1; letter-spacing: .04em;
  }
  .company-dot { border-radius: 50%; background: var(--orange); display: inline-block; flex: none; }
  .accent { color: var(--orange); }

  /* front */
  .card-front .company-name {
    position: absolute; left: 50%; top: 165px; transform: translateX(-50%);
    font-size: 48px;
  }
  .card-front .company-dot { width: 22px; height: 22px; }
  .front-web {
    position: absolute; left: 0; right: 0; bottom: 40px; text-align: center;
    font-size: 16px; letter-spacing: .06em;
  }

  /* back */
  .holder { position: absolute; left: 48px; top: 44px; }
  .holder-name { font-size: 32px; font-weight: 800; letter-spacing: .02em; }
  .holder-title { font-size: 17px; font-weight: 600; color: var(--orange); margin-top: -4px; }
  .details {
    position: absolute; left: 48px; top: 170px;
    font-size: 18px; font-weight: 300; line-height: 1.35; letter-spacing: .03em;
  }
  .license { margin-bottom: 8px; }
  .license .accent { font-weight: 400; }
  .address { margin-bottom: 8px; }
  .contact-list { list-style: none; }
  .contact-list li { display: flex; align-items: center; gap: 14px; height: 27px; }
  .contact-list svg { width: 16px; height: 16px; flex: none; }
  .card-back .company-name {
    position: absolute; right: 48px; bottom: 60px;
    font-size: 42px;
  }
  .card-back .company-dot { width: 20px; height: 20px; }
</style>
</head>
<body>
<main class="canvas">
  <section class="card card-front">
    <div class="company-name"><span class="company-dot"></span>Corvane</div>
    <div class="front-web">www.<span class="accent">corvane-hvac</span>.com</div>
  </section>

  <section class="card card-back">
    <div class="holder">
      <h1 class="holder-name">Walter Brinoku</h1>
      <p class="holder-title">Home comfort consultant</p>
    </div>
    <div class="details">
      <p class="license"><span class="accent">Lic#</span>584261</p>
      <p class="address">4827 Dunmore St #215<br>Oakland, CA 94619</p>
      <ul class="contact-list">
        <li>
          <svg viewBox="0 0 16 16" fill="none" stroke="var(--orange)" stroke-width="1.6"><rect x="4" y="1" width="8" height="14" rx="1.5"/><line x1="7" y1="12.5" x2="9" y2="12.5"/></svg>
          888-316-2790
        </li>
        <li>
          <svg viewBox="0 0 16 16" fill="var(--orange)"><path d="M3 1.5l2.5-.5 1.5 3.5-1.5 1.2c.8 1.8 2 3 3.8 3.8L10.5 8l3.5 1.5-.5 2.5C13 14 11 14.5 9 13.5 5.5 12 3.9 10.4 2.5 7 1.6 4.8 2 2.8 3 1.5z"/></svg>
          510-742-3185
        </li>
        <li>
          <svg viewBox="0 0 16 16" fill="none" stroke="var(--orange)" stroke-width="1.5"><rect x="1" y="3" width="14" height="10"/><polyline points="1,3 8,9 15,3"/></svg>
          walter@corvane-hvac.com
        </li>
        <li>
          <svg viewBox="0 0 16 16" fill="none" stroke="var(--orange)" stroke-width="1.2"><circle cx="8" cy="8" r="6.5"/><ellipse cx="8" cy="8" rx="3" ry="6.5"/><line x1="1.5" y1="8" x2="14.5" y2="8"/><line x1="2.5" y1="4.5" x2="13.5" y2="4.5"/><line x1="2.5" y1="11.5" x2="13.5" y2="11.5"/></svg>
          <span>www.<span class="accent">corvane-hvac</span>.com</span>
        </li>
      </ul>
    </div>
    <div class="company-name"><span class="company-dot"></span>Corvane</div>
  </section>
</main>
</body>
</html>
```